The design should look similar to the uploaded example to accommodate the information needed for a business card template. I would like to see the colors orange and charcoal grey incorporated along with the logo.The following should be on the back of the card SPECIALIZING IN NEW AND USED TIRES & WHEELS FOR:- Loaders- Skid Steers- Telehandlers- Boom Lifts- Forklifs and moreELIMINATING DOWNTIMEWheel Exchange Program for New & Used Foam Filled and Solid Rubber TiresSPECIALTY SERVICES- Foam Filling Tires- Largest Tire Press in SE- ONSITE Forklift Tire Press- Boom Truck Services - Rubber Tracks

Target Market(s)

New and Existing Customers

Industry/Entity Type

Business

Contact Information for Business Card

NAMEHEAVY DUTY TIRE, LLC8470 Belvedere RoadWest Palm Beach, FL 33411P: 844-HD-TIRESF: 561-431-6469C:E: W: WWW.GRANITERIMSUPPLY-EXAMPLE.COM

Font styles to use
Sans Serif

Colors
f37122
333333

Requirements
Must have
• The logo and the information indicated for the backside of the card
Nice to have
• Keep the orange and charcoal grey colors

```html
<!DOCTYPE html>
<html lang="en">
<head>
<meta charset="utf-8">
<title>Granite Rim Supply, LLC — Business Card</title>
<link rel="stylesheet" href="https://fonts.googleapis.com/css2?family=Arvo:wght@700&family=PT+Sans:ital,wght@0,400;0,700;1,400&display=swap">
<style>
  :root {
    --orange: #f37122;
    --charcoal: #333a3b;
    --ink: #2f3536;
    --paper: #f3f3f4;
    --backdrop: #9b9b9b;
    --light-text: #e6e8e8;
  }
  * { box-sizing: border-box; margin: 0; padding: 0; }
  html, body {
    width: 1105px; height: 1200px; overflow: hidden;
    background: var(--backdrop);
  }
  .card {
    position: absolute; left: 182px; width: 747px; height: 425px;
  }
  .card--front { top: 120px; background: var(--paper); color: var(--ink); }
  .card--back { top: 637px; background: var(--charcoal); color: var(--light-text); text-align: center; }

  .brand {
    position: absolute; left: 43px; top: 48px;
    display: flex; align-items: center; gap: 10px;
  }
  .brand__dot {
    width: 70px; height: 70px; border-radius: 50%; background: var(--orange);
  }
  .brand__name {
    font-family: "Arvo", Georgia, serif; font-weight: 700;
    font-size: 24px; line-height: 1.15; color: var(--ink); letter-spacing: 0.5px;
  }

  .contact {
    position: absolute; left: 50px; top: 180px;
    font-family: "PT Sans", Arial, sans-serif; font-size: 20px; line-height: 28px; color: #3d4344;
    list-style: none;
  }
  .contact__item { display: flex; align-items: center; }
  .contact__item svg { width: 18px; height: 18px; margin: 0 12px 0 2px; fill: var(--ink); }

  .person {
    position: absolute; right: 50px; top: 288px; text-align: right;
  }
  .person__name {
    font-family: "Arvo", Georgia, serif; font-weight: 700; font-size: 27px; color: var(--ink); letter-spacing: 0.5px;
  }
  .person__title {
    font-family: "Arvo", Georgia, serif; font-weight: 700; font-size: 19px; color: var(--orange); letter-spacing: 0.5px;
  }
  .accent-bar {
    position: absolute; right: 0; top: 291px; width: 18px; height: 54px; background: var(--charcoal);
  }

  .back-brand { padding-top: 26px; display: flex; flex-direction: column; align-items: center; gap: 12px; }
  .back-brand__dot { width: 100px; height: 100px; border-radius: 50%; background: var(--orange); }
  .back-brand__name {
    font-family: "Arvo", Georgia, serif; font-weight: 700; font-size: 22px; line-height: 28px; color: var(--light-text); letter-spacing: 1px;
  }
  .services { font-family: "PT Sans", Arial, sans-serif; margin-top: 24px; }
  .services__heading { font-weight: 700; font-size: 20px; line-height: 27px; letter-spacing: 0.3px; }
  .services__line { font-size: 19.5px; line-height: 27px; }
  .services__line--italic { font-style: italic; }
  .services__group + .services__group { margin-top: 14px; }
  .sep { color: var(--orange); padding: 0 4px; }
</style>
</head>
<body>

<section class="card card--front">
  <div class="brand">
    <div class="brand__dot"></div>
    <div class="brand__name">GRANITE RIM<br>SUPPLY, LLC</div>
  </div>

  <ul class="contact">
    <li>5126 Marston Lane</li>
    <li>Cedar Hollow, FL 33920</li>
    <li class="contact__item">
      <svg viewBox="0 0 24 24" aria-hidden="true"><path d="M6.6 10.8a15.2 15.2 0 0 0 6.6 6.6l2.2-2.2a1 1 0 0 1 1-.25 11.4 11.4 0 0 0 3.6.57 1 1 0 0 1 1 1V20a1 1 0 0 1-1 1A17 17 0 0 1 3 4a1 1 0 0 1 1-1h3.5a1 1 0 0 1 1 1c0 1.250.2 2.450.57 3.57a1 1 0 0 1-.25 1z"/></svg>
      844-GR-WHEEL
    </li>
    <li class="contact__item">
      <svg viewBox="0 0 24 24" aria-hidden="true"><path d="M7 1h10a2 2 0 0 1 2 2v18a2 2 0 0 1-2 2H7a2 2 0 0 1-2-2V3a2 2 0 0 1 2-2zm0 3v14h10V4zm5 15.5a1 1 0 1 0 0 2 1 1 0 0 0 0-2z"/></svg>
      836 512 7740
    </li>
    <li class="contact__item">
      <svg viewBox="0 0 24 24" aria-hidden="true"><path d="M6 2h10l2 2v5H6zM3 10h18a2 2 0 0 1 2 2v8H1v-8a2 2 0 0 1 2-2zm3 6v3h12v-3z"/></svg>
      561-278-9053
    </li>
    <li class="contact__item">
      <svg viewBox="0 0 24 24" aria-hidden="true"><path d="M2 5h20v14H2zm2 2v.5l8 5 8-5V7z"/></svg>
      hello@graniterim-example.com
    </li>
    <li class="contact__item">
      <svg viewBox="0 0 24 24" aria-hidden="true"><path d="M12 2a10 10 0 1 0 0 20 10 10 0 0 0 0-20zm6.9 6h-3a15 15 0 0 0-1.4-3.9A8 8 0 0 1 18.9 8zM12 4c.8 1.2 1.5 2.5 1.9 4h-3.8c.4-1.5 1.1-2.8 1.9-4zM4.3 14a8 8 0 0 1 0-4h3.4a16 16 0 0 0 0 4zm.8 2h3a15 15 0 0 0 1.4 3.9A8 8 0 0 1 5.1 16zm3-8h-3a8 8 0 0 1 4.4-3.9A15 15 0 0 0 8.1 8zM12 20c-.8-1.2-1.5-2.5-1.9-4h3.8c-.4 1.5-1.1 2.8-1.9 4zm2.3-6H9.7a14 14 0 0 1 0-4h4.6a14 14 0 0 1 0 4zm.2 5.9a15 15 0 0 0 1.4-3.9h3a8 8 0 0 1-4.4 3.9zm1.8-5.9a16 16 0 0 0 0-4h3.4a8 8 0 0 1 0 4z"/></svg>
      www.graniterimsupply-example.com
    </li>
  </ul>

  <div class="person">
    <div class="person__name">DANIEL REYES</div>
    <div class="person__title">CEO/FOUNDER</div>
  </div>
  <div class="accent-bar"></div>
</section>

<section class="card card--back">
  <div class="back-brand">
    <div class="back-brand__dot"></div>
    <div class="back-brand__name">GRANITE RIM SUPPLY</div>
  </div>

  <div class="services">
    <div class="services__group">
      <h2 class="services__heading">SPECIALIZING IN NEW AND USED TIRES &amp; WHEELS FOR</h2>
      <p class="services__line services__line--italic">Loaders<span class="sep">•</span>Skid Steers<span class="sep">•</span>Telehandlers<span class="sep">•</span>Boom Lifts<span class="sep">•</span>Forklifs and more</p>
    </div>
    <div class="services__group">
      <h2 class="services__heading">ELIMINATING DOWNTIME</h2>
      <p class="services__line">Wheel Exchange Program for New &amp; Used Foam Filled and Solid Rubber Tires</p>
    </div>
    <div class="services__group">
      <h2 class="services__heading">SPECIALTY SERVICES</h2>
      <p class="services__line services__line--italic">Foam Filling Tires<span class="sep">•</span>Largest Tire Press in SE<span class="sep">•</span>ONSITE Forklift Tire Press</p>
      <p class="services__line services__line--italic">Boom Truck Services<span class="sep">•</span>Rubber Tracks</p>
    </div>
  </div>
</section>

</body>
</html>
```